Redesign company trifold brochure

We are rebranding our company in September and looking for a more professional design for our brochure.

What we do - providing interdisciplinary care for those supporting ill, elderly and special needs pets at home following the human hospice model of care - is very novel and our brochure is key in explaining it and our offerings.

We serve dogs and cats. Most of the animals are quite sick, elderly. I have many personal and stock photos we can use in the brochure. Please - no pictures of puppies and/or kittens.

The hard part is fitting the info and message into a clear and concise format.

It must be appealing both to pet owners and vets (who are our primary source of patients through referrals).

It should covey WARMTH, COMPASSION, PROFESSIONALISM, and EXPERTISE.

Please look at our website www.TrellisAnimalRespite.com for more info

We have until now used maroon and copper for colors - to reflect the "sunset" of the pets life. BUT are now changing to Navy, Teal and White to reflect calm, trust and competence.

We will use the same logo recolored.

Existing brochure and new logo are attached.

PLEASE ask questions!!
Updates

We have a library of stock images you are welcome to use. All have been legally acquired and we have the right to use them. You DO NOT have to use them, just sending along in case you wish to. https://www.filecrate.example/sh/qk4vrm82zd1pyno/KLQ7Ztbn-Rrfx2mh9sWpYJ4Dc?dl=0

Our colors are NAVY, TEAL and WHITE. For your reference, the navy we use is 99/87/44/55 (CMYK) The Teal we use is 76/11/44/0 (CMYK) Thank you!

Designers -- pleaseuse pictures of older pets (no puppies or kittens). Below is a link to stock photos we own that would be appropriate for use in the brochure. https://www.filecrate.example/sh/w274m6t9pxkr5da/KLRn3GsfwlTVBXEPcq_8ZNj5u?dl=0 THANK YOU!

Designers -- I would VERY much like to include a photo of a pet in a wheel chair. I have personal photos as well as (purchased) stock photos for this purpose which can be found at http://lnk.example/TARHC-Pets-in-Wheelchairs Thank you!!

Today is the last day! Many of you have submitted beautiful designs and others are rolling in. I am so appreciative of your time and energy!! Please do not let the deadline pass without YOUR very BEST entry being submitted!! Thank you! - Miriam & All of us at Trellis Animal Respite & Home Care

Target Market(s)

Pet Owners and Veterinarians

Industry/Entity Type

Pet Care

Font styles to use
Serif

Colors
0455a3
33b8a4
ffffff

Requirements
Must have
• Our logo and information about our services. Pictures of pets. Our contact info. PLEASE NOTE: this is a 2 sided brochure. Please submit both inside and outside.
Should not have
• puppies, kittens - anything off message

```html
<!DOCTYPE html>
<html lang="en">
<head>
<meta charset="utf-8">
<title>Trellis Animal Respite &amp; Home Care – Brochure Inside</title>
<link href="https://fonts.googleapis.com/css2?family=Arimo:wght@400;700&family=Comfortaa:wght@300;400&family=Dancing+Script:wght@500;600&display=swap" rel="stylesheet">
<style>
  :root {
    --blue: #1f5bd8;
    --blue-deep: #1848b8;
    --navy: #1f3a7a;
    --teal: #33b8a4;
    --teal-bright: #5fe0a8;
    --panel-grey: #f2f3f5;
    --white: #ffffff;
    --photo-green: #6f9a3c;
    --photo-gold: #c98a3a;
  }
  html, body { margin: 0; padding: 0; overflow: hidden; background: var(--white); }
  .brochure {
    position: relative; width: 1200px; height: 930px; overflow: hidden;
    background: var(--white); font-family: "Arimo", Arial, sans-serif; color: var(--navy);
  }
  .backdrop { position: absolute; inset: 0; }
  .block { position: absolute; margin: 0; }
  .script { font-family: "Dancing Script", cursive; font-weight: 600; }

  /* Left panel */
  .care-title { left: 88px; top: 404px; font-size: 30px; color: var(--white); font-weight: 500; }
  .care-copy { left: 60px; top: 446px; width: 400px; font-size: 16px; line-height: 22px; color: var(--white); }
  .care-copy p { margin: 0 0 10px; }
  .care-copy strong { text-decoration: underline; }
  .both-title { left: 102px; top: 573px; font-size: 23px; color: var(--white); text-decoration: underline; text-underline-offset: 4px; }
  .both-list { left: 100px; top: 616px; width: 380px; font-size: 15px; color: var(--white); font-weight: 700; }

  .icon-list { list-style: none; margin: 0; padding: 0; }
  .icon-list li { position: relative; padding-left: 32px; }
  .icon-list li svg { position: absolute; left: 0; top: 2px; width: 22px; height: 14px; }
  .both-list li { margin-bottom: 15px; line-height: 19px; }

  /* Middle panel */
  .services-title { left: 518px; top: 356px; font-family: "Comfortaa", sans-serif; font-weight: 300; font-size: 37px; color: var(--teal); letter-spacing: 1px; }
  .services-rule { left: 518px; top: 405px; width: 232px; height: 2px; background: var(--blue); }
  .services-intro { left: 520px; top: 418px; width: 282px; font-size: 16px; line-height: 24px; }
  .available { left: 518px; top: 517px; width: 270px; height: 131px; background: var(--teal-bright);
    color: var(--white); font-size: 21px; line-height: 30px; text-align: center; display: flex; align-items: center; justify-content: center; padding: 0 8px; box-sizing: border-box; }
  .services-list { left: 520px; top: 666px; width: 290px; font-size: 16px; line-height: 21px; }
  .services-list li { margin-bottom: 13px; }
  .services-extra { left: 450px; top: 822px; width: 340px; font-size: 16px; line-height: 22px; }

  /* Right panel */
  .offer-list { left: 805px; top: 30px; width: 390px; font-size: 16px; line-height: 21px; }
  .offer-list li { margin-bottom: 14px; }
  .skilled-title { left: 812px; top: 276px; width: 282px; border-top: 2px solid var(--navy); border-bottom: 2px solid var(--navy);
    font-size: 23px; line-height: 26px; padding: 6px 0; font-style: italic; }
  .skilled-list { left: 836px; top: 352px; width: 300px; font-size: 16px; color: var(--teal); }
  .skilled-list li { height: 30px; line-height: 22px; }
  .team-title { left: 826px; top: 699px; width: 282px; border-top: 2px solid var(--navy); text-align: center; font-size: 33px; padding-top: 4px; }
  .team-lead { left: 815px; top: 752px; width: 320px; text-align: center; font-size: 22px; color: var(--teal); }
  .team-intro { left: 815px; top: 782px; width: 320px; text-align: center; font-size: 16px; }
  .team-list { left: 808px; top: 812px; list-style: none; padding: 0; font-size: 16px; }
  .team-list li { position: relative; padding-left: 24px; height: 30px; }
  .team-list li::before { content: ""; position: absolute; left: 4px; top: 6px; width: 8px; height: 8px; border-radius: 50%; background: var(--blue); }
</style>
</head>
<body>
<main class="brochure">
  <svg class="backdrop" width="1200" height="930" viewBox="0 0 1200 930" aria-hidden="false">
    <defs>
      <linearGradient id="fieldTone" x1="0" y1="0" x2="1" y2="1">
        <stop offset="0" stop-color="#a9c46a"/>
        <stop offset="0.45" stop-color="var(--photo-gold)"/>
        <stop offset="1" stop-color="var(--photo-green)"/>
      </linearGradient>
      <radialGradient id="catTone" cx="0.5" cy="0.5" r="0.6">
        <stop offset="0" stop-color="#e9c9a8"/>
        <stop offset="0.6" stop-color="#c98a52"/>
        <stop offset="1" stop-color="#8f6a4a"/>
      </radialGradient>
      <symbol id="arrow-mark" viewBox="0 0 22 14">
        <path d="M2 7 H16 M11 2 L17 7 L11 12" fill="none" stroke="currentColor" stroke-width="2" stroke-linecap="round" stroke-linejoin="round"/>
      </symbol>
    </defs>

    <rect x="802" y="0" width="398" height="930" fill="var(--panel-grey)"/>

    <path role="img" aria-label="Photo of an older golden retriever resting on green grass"
          d="M0 0 H780 C640 150 560 260 450 420 L0 420 Z" fill="url(#fieldTone)"/>

    <path d="M780 0 C640 150 555 265 440 420 C560 290 650 170 800 0 Z" fill="var(--blue)"/>
    <path d="M805 0 C680 140 600 250 520 340" fill="none" stroke="var(--blue)" stroke-width="2"/>

    <circle cx="600" cy="82" r="140" fill="none" stroke="var(--blue)" stroke-width="2"/>
    <circle cx="600" cy="82" r="132" fill="var(--white)"/>
    <circle role="img" aria-label="Photo of a senior ginger cat" cx="600" cy="82" r="124" fill="url(#catTone)"/>

    <circle cx="215" cy="650" r="312" fill="none" stroke="var(--blue)" stroke-width="2"/>
    <circle cx="215" cy="650" r="300" fill="var(--blue)"/>

    <path d="M960 930 C1060 900 1140 860 1200 820 V930 Z" fill="var(--blue)"/>
    <path d="M900 930 C1010 905 1120 860 1200 800 V812 C1120 868 1020 912 930 930 Z" fill="var(--blue-deep)" opacity="0.5"/>
  </svg>

  <h2 class="block care-title script">Palliative Care and Hospice</h2>
  <div class="block care-copy">
    <p><strong>Palliative Care</strong> seeks to relieve suffering and improve quality of life at all stages of illness, injury and disease, whether curable or not.</p>
    <p style="font-size:14px;line-height:19px"><strong>Hospice</strong> is a special kind of Palliative Care focused on those with a life expectancy of less than one year.</p>
  </div>
  <h3 class="block both-title script">Both Palliative Care and Hospice:</h3>
  <ul class="block icon-list both-list">
    <li><svg><use href="#arrow-mark"/></svg>Focus on living fully</li>
    <li><svg><use href="#arrow-mark"/></svg>Recognize and address all suffering – physical, emotional, social and spiritual</li>
    <li><svg><use href="#arrow-mark"/></svg>Use a team approach to meet the needs of the animal and his or her family</li>
    <li><svg><use href="#arrow-mark"/></svg>Affirm life while viewing death as a natural, normal process</li>
  </ul>

  <h2 class="block services-title">Our Services</h2>
  <div class="block services-rule"></div>
  <p class="block services-intro">At Trellis Animal Respite &amp; Home Care, our only goal is to support you in providing the very best care for your beloved companion in your own home.</p>
  <p class="block available">We are here for you 24 hours a day, every day of the year.</p>
  <ul class="block icon-list services-list" style="color:var(--navy)">
    <li><svg style="color:var(--blue)"><use href="#arrow-mark"/></svg>Visiting and support</li>
    <li><svg style="color:var(--blue)"><use href="#arrow-mark"/></svg>Administration of medication &amp; fluids</li>
    <li><svg style="color:var(--blue)"><use href="#arrow-mark"/></svg>Overnight and respite care</li>
    <li><svg style="color:var(--blue)"><use href="#arrow-mark"/></svg>Check-ins, exercise and play</li>
  </ul>
  <ul class="block icon-list services-extra">
    <li><svg style="color:var(--blue)"><use href="#arrow-mark"/></svg>Assistance evaluating pain, quality of life, and end of life choices</li>
  </ul>

  <ul class="block icon-list offer-list">
    <li><svg style="color:var(--blue)"><use href="#arrow-mark"/></svg>Coordination of care with your vet and other care professionals</li>
    <li><svg style="color:var(--blue)"><use href="#arrow-mark"/></svg>Home cooked meals and treats</li>
    <li><svg style="color:var(--blue)"><use href="#arrow-mark"/></svg>Transportation and errand running</li>
    <li><svg style="color:var(--blue)"><use href="#arrow-mark"/></svg>Equipment and supplies</li>
    <li><svg style="color:var(--blue)"><use href="#arrow-mark"/></svg>Funerals and memorials</li>
    <li><svg style="color:var(--blue)"><use href="#arrow-mark"/></svg>Bereavement support</li>
  </ul>

  <h3 class="block skilled-title script">Our skilled team members can also provide:</h3>
  <ul class="block icon-list skilled-list">
    <li><svg><use href="#arrow-mark"/></svg>Bereavement support</li>
    <li><svg><use href="#arrow-mark"/></svg>Cold LASER Treatments</li>
    <li><svg><use href="#arrow-mark"/></svg>Reiki</li>
    <li><svg><use href="#arrow-mark"/></svg>Passive Range of Motion (PROM)</li>
    <li><svg><use href="#arrow-mark"/></svg>Rehabilitation Support</li>
    <li><svg><use href="#arrow-mark"/></svg>Grooming</li>
    <li><svg><use href="#arrow-mark"/></svg>Essential Oils</li>
    <li><svg><use href="#arrow-mark"/></svg>Bach Flower Essences</li>
    <li><svg><use href="#arrow-mark"/></svg>Aroma Therapy</li>
    <li><svg><use href="#arrow-mark"/></svg>Music Therapy</li>
    <li><svg><use href="#arrow-mark"/></svg>Pet Therapy</li>
  </ul>

  <h2 class="block team-title script">Our Team</h2>
  <p class="block team-lead">Lead by Miriam Okafor, C.T.</p>
  <p class="block team-intro">our interdisciplinary team includes:</p>
  <ul class="block team-list">
    <li>Certified Thanatologi</li>
    <li>Certified Veterinary Technicians</li>
  </ul>
</main>
</body>
</html>
```